Homepage for the brisk-find Web Application

At the end of this text, you will find a link to a website that is under construction for a webApp that I intend to launch soon. The contest goal is for you to make redesign the homepage in a nice, fresh, modern Style. Only design, no coding necessary. It needs to have a responsive version for small screens like smart phones. Attached is the text for it, and some images that you may use. You are welcome to find or create additional supporting images. You can use PixTrove.example or similar service to find new images as long as I can purchase the non-exclusive use rights for the images at similar prices. The contest is just for the home page. However, the winner, if I like the work and we can agree on a fair price, could be contracted on a one-on-one basis to do the rest of the site. You are welcome to suggest minor changes like font sizes and minor variations on the Header banner, but that banner is consistent with the user interface of the application therefore should not change too much. The information should flow somewhat continually without much use of side bars or things like that.
https://www.brisk-find.example
Sincerely,
Marco D. Ferral

```html
<!DOCTYPE html>
<html lang="en">
<head>
<meta charset="utf-8">
<title>Brisk Find — Homepage</title>
<link rel="stylesheet" href="https://fonts.googleapis.com/css2?family=Roboto:wght@300;400;500;700&display=swap">
<style>
  :root {
    --accent: #e4572e;
    --blue: #2e7bc4;
    --mint: #d6f9fa;
    --teal: #2eb5c5;
    --ink: #222;
    --sand: #e6d6cc;
    --coral: #ff7b55;
    --deep-teal: #1c8fae;
    --white: #ffffff;
  }
  * { margin: 0; padding: 0; box-sizing: border-box; }
  html, body {
    width: 1200px; height: 2500px; overflow: hidden;
    background: var(--white);
    font-family: "Roboto", sans-serif;
  }
  .page {
    position: absolute; left: 124px; top: 0;
    width: 980px; height: 2576px;
    transform: scale(0.9705); transform-origin: 0 0;
    background: var(--white);
  }
  .abs { position: absolute; }

  .site-header {
    left: 0; top: 0; width: 980px; height: 128px;
    background: linear-gradient(90deg, #ffffff 0%, #b9d2ea 25%, #5f9bd3 55%, var(--blue) 72%, var(--blue) 100%);
  }
  .brand { left: 20px; top: 34px; display: flex; align-items: center; gap: 8px; }
  .brand-dot { width: 42px; height: 42px; border-radius: 50%; border: 4px solid #444; }
  .brand-name { font-size: 34px; font-weight: 400; color: var(--accent); letter-spacing: 0.5px; }
  .field {
    height: 21px; width: 258px; top: 54px;
    background: var(--mint); border-radius: 11px;
    font-size: 11.5px; letter-spacing: 1.5px; color: #333;
    padding: 3px 12px;
  }
  .field-user { left: 257px; }
  .field-pass { left: 527px; }
  .login-btn {
    left: 827px; top: 50px; width: 86px; height: 29px;
    background: var(--white); border-radius: 14px;
    color: var(--accent); font-weight: 700; font-size: 13px; letter-spacing: 2px;
    display: flex; align-items: center; justify-content: center;
  }

  .main-nav { left: 0; top: 128px; width: 980px; height: 60px; }
  .main-nav a {
    position: absolute; top: 18px;
    color: var(--accent); text-decoration: none;
    font-size: 17px; letter-spacing: 2.4px;
  }

  .hero-bg { left: 0; top: 128px; }
  .hero-art {
    left: 48px; top: 262px; width: 408px; height: 456px;
    border-radius: 46% 40% 42% 48% / 30% 44% 50% 40%;
    background: radial-gradient(ellipse at 48% 52%, #7fd0dc 0%, #b8e0e2 45%, var(--sand) 80%);
  }
  .hero-title {
    left: 480px; top: 358px; width: 470px; text-align: center;
    color: var(--accent); font-weight: 700; font-size: 42px; line-height: 49px; letter-spacing: 5px;
  }
  .divider { left: 411px; top: 796px; width: 172px; height: 4px; background: var(--accent); }

  .blob { left: 0; }
  .section-title {
    width: 980px; left: 0; text-align: center;
    color: var(--accent); font-weight: 500; font-size: 25px; line-height: 30px; letter-spacing: 3.6px;
  }
  .copy {
    font-size: 17px; line-height: 25.8px; letter-spacing: 2.2px; color: var(--ink); font-weight: 400;
    white-space: nowrap;
  }
  .copy strong { font-weight: 700; letter-spacing: 2px; }
  .pill {
    background: var(--teal); color: var(--white); border-radius: 27px;
    display: flex; align-items: center; justify-content: center;
    font-size: 19px; font-weight: 500; letter-spacing: 3px;
    box-shadow: 0 5px 8px rgba(0,0,0,0.18);
    text-decoration: none;
  }
  .benefits { list-style: none; }
  .benefits li { margin-bottom: 8.5px; }

  .site-footer {
    left: 0; top: 2507px; width: 980px; height: 69px; background: var(--blue);
    color: var(--white); font-weight: 700; font-size: 14px; letter-spacing: 2.4px;
  }
  .site-footer span { position: absolute; top: 27px; }
</style>
</head>
<body>
<div class="page">

  <header class="site-header abs">
    <div class="brand abs"><span class="brand-dot"></span><span class="brand-name">Brisk Find</span></div>
    <div class="field field-user abs">username</div>
    <div class="field field-pass abs">password</div>
    <div class="login-btn abs">LOGIN</div>
  </header>

  <svg class="hero-bg abs" width="980" height="600" viewBox="0 0 980 600">
    <path fill="#d6f9fa" d="M0,0 H980 V305 C955,420 870,560 700,568 C560,575 420,545 370,470 C320,400 220,280 120,290 C60,296 20,312 0,320 Z"/>
  </svg>
  <div class="hero-art abs" role="img" aria-label="Illustration: a person taking an item out of a file drawer that slides from a smartphone"></div>

  <nav class="main-nav abs">
    <a href="#" style="left:85px">About</a>
    <a href="#" style="left:170px">Pricing</a>
    <a href="#" style="left:274px">Blog</a>
    <a href="#" style="left:358px">FAQs</a>
    <a href="#" style="left:444px">Support</a>
    <a href="#" style="left:560px">Review</a>
    <a href="#" style="left:660px">Contact Us</a>
    <a href="#" style="left:797px">Free-Trial</a>
  </nav>

  <h1 class="hero-title abs">Find that<br>document or item<br>instantly.</h1>
  <div class="divider abs"></div>

  <svg class="blob abs" style="top:885px" width="980" height="390" viewBox="0 0 980 390">
    <path fill="#d6f9fa" d="M250,5 C300,-10 340,20 390,40 C470,70 570,10 650,5 C800,-5 890,90 885,200 C880,280 800,330 620,325 C500,380 300,400 200,360 C120,330 110,260 110,180 C110,90 180,25 250,5 Z"/>
  </svg>
  <h2 class="section-title abs" style="top:923px">Keeping track of all your paper documents and other<br>belongings has never been easier.</h2>
  <p class="copy abs" style="left:127px; top:1028px">Brisk-Find is a system that allows you to quickly search for the location<br>of every item that you store or file. It is an essential tool for keeping<br>track of paper documents. In addition, it is incredibly valuable for storing<br>any other kind of physical items. Giving you the ability to quickly find any<br>item, even years after it has been stored. More importantly, using<br>Brisk-Find along with some best practice techniques, could allow you to<br>save considerable space without losing fast accessibility of your items.</p>

  <svg class="blob abs" style="top:1340px" width="980" height="585" viewBox="0 0 980 585">
    <path fill="#d6f9fa" d="M210,15 C320,80 520,85 690,25 C800,-20 920,30 935,105 C940,135 920,140 900,150 C860,180 860,230 875,250 C885,320 875,400 860,450 C835,540 700,575 520,578 C330,580 170,530 90,390 C30,290 40,160 90,90 C130,30 180,0 210,15 Z"/>
  </svg>
  <h2 class="section-title abs" style="top:1428px">Why use a storage management system like<br>Brisk-Find?</h2>
  <p class="copy abs" style="left:117px; top:1540px"><strong>Managing paper documents</strong><br>It is quite common for most people and businesses to receive a variety of<br>such documents that need to be filed. The problem is how to efficiently do<br>it in a way that any of it can easily be found, even in a distant future. We<br>normally put them in folders on file drawers sorted by some criteria. But<br>which criterion is the right standard for all kinds of documents? There is<br>no right criterion for every kind of document.</p>
  <a class="pill abs" href="#" style="left:403px; top:1771px; width:174px; height:53px">read more</a>

  <svg class="blob abs" style="top:1965px" width="980" height="545" viewBox="0 0 980 545">
    <path fill="#d6f9fa" d="M0,120 C60,90 150,80 200,110 C260,150 320,160 420,110 C520,50 620,0 720,0 C830,0 930,100 980,175 V545 H0 Z"/>
  </svg>
  <h2 class="section-title abs" style="top:2043px">Why Brisk-Find?</h2>
  <ul class="benefits copy abs" style="left:152px; top:2112px">
    <li>• It is extremely easy to use.</li>
    <li>• It is Versatile. Since each catalog can have 1 or many levels of depth<br>(folders and sub-folders). Brisk-Find does not force you to use a specific<br>filing or storage methodology.</li>
    <li>• It is really affordable. Checkout our pricing plans.</li>
    <li>• Since it is online, your data is available almost anywhere in the world.</li>
    <li>• Your data always travels encrypted.</li>
  </ul>
  <a class="pill abs" href="#" style="left:206px; top:2388px; width:258px; height:53px">check our pricing</a>
  <a class="pill abs" href="#" style="left:558px; top:2387px; width:274px; height:53px">start 30 days trial</a>

  <footer class="site-footer abs">
    <span style="left:30px">-- contact --</span>
    <span style="left:325px">Copyright © 2016 Vellum Works LLC</span>
    <span style="left:802px">-- social media --</span>
  </footer>

</div>
</body>
</html>
```